Design a New Business Card for Our Company

We are looking for fresh, unique, and a modern business card that reflects our roots as digital marketing agency focused on SEM.

Industry/Entity Type

Marketing

Contact Information for Business Card

looking for very unique out of the box designs. clean and modern that compliments our logo

Requirements
Must have
• colors should match our logo
• Front should have name, address, email, and phone/fax of the person, phone/fax are the same number
• back should have our url

```html
<!DOCTYPE html>
<html lang="en">
<head>
<meta charset="utf-8">
<title>Brightmere Solutions — Business Card</title>
<link rel="stylesheet" href="https://fonts.googleapis.com/css2?family=Open+Sans:wght@400;600;700&family=Montserrat:wght@500&display=swap">
<style>
  :root {
    --page: #e9eaec;
    --frost: #f3f4f6;
    --frost-edge: #dfe2e6;
    --brand-blue: #5b97d2;
    --brand-grey: #a9abad;
    --ink-light: #ffffff;
    --ghost: rgba(91, 151, 210, 0.28);
  }
  * { margin: 0; padding: 0; box-sizing: border-box; }
  html, body {
    width: 1200px; height: 900px; overflow: hidden;
    background: var(--page);
    font-family: "Open Sans", Arial, sans-serif;
  }
  .canvas { position: relative; width: 1200px; height: 900px; }

  .card {
    position: absolute;
    width: 556px; height: 343px;
    box-shadow: 0 6px 18px rgba(0,0,0,0.12);
    overflow: hidden;
  }
  .card--front { left: 238px; top: 62px; }
  .card--back  { left: 457px; top: 518px; width: 560px; }

  .card__frost {
    position: absolute; left: 0; top: 0; right: 0;
    height: 185px;
    background: linear-gradient(180deg, var(--frost), var(--frost-edge));
  }
  .card__band {
    position: absolute; left: 0; right: 0; bottom: 0;
    height: 158px;
    background: var(--brand-blue);
    color: var(--ink-light);
  }
  .card--back .card__frost { height: 187px; }
  .card--back .card__band { height: 156px; }

  /* Wordmark */
  .wordmark {
    position: absolute; left: 96px; top: 52px;
    display: flex; align-items: center; gap: 14px;
  }
  .wordmark__dot {
    width: 56px; height: 56px; border-radius: 50%;
    background: var(--brand-blue);
  }
  .wordmark__name {
    font-weight: 600; font-size: 52px; line-height: 1;
    color: var(--brand-blue); letter-spacing: -1px;
  }

  .wordmark--ghost {
    left: auto; right: 100px; top: 58px;
    transform: scaleX(-1);
  }
  .wordmark--ghost .wordmark__dot { background: var(--ghost); }
  .wordmark--ghost .wordmark__name { color: var(--ghost); }

  /* Person details */
  .person {
    position: absolute; right: 298px; top: 38px;
    text-align: right; white-space: nowrap;
  }
  .person__name { font-weight: 700; font-size: 17px; line-height: 22px; }
  .person__role { font-size: 14.5px; line-height: 20px; margin-bottom: 8px; }
  .person__address { font-size: 14.5px; line-height: 21px; }

  .contact {
    position: absolute; left: 279px; top: 48px;
    list-style: none; font-size: 14.5px; line-height: 20px;
  }
  .contact li { display: flex; align-items: center; gap: 8px; }
  .contact svg { width: 11px; height: 11px; fill: var(--ink-light); }

  .site {
    position: absolute; left: 0; right: 0; bottom: 38px;
    text-align: center;
    font-family: "Montserrat", Arial, sans-serif;
    font-weight: 500; font-size: 17px; letter-spacing: 1.5px;
  }
</style>
</head>
<body>
<main class="canvas">

  <section class="card card--front" aria-label="Business card front">
    <div class="card__frost">
      <div class="wordmark">
        <span class="wordmark__dot"></span>
        <span class="wordmark__name">Brightmere</span>
      </div>
    </div>
    <div class="card__band">
      <div class="person">
        <p class="person__name">Daniel Harper</p>
        <p class="person__role">Managing Director</p>
        <p class="person__address">48 Harbour Lane</p>
        <p class="person__address">Eastbridge, 20418.</p>
      </div>
      <ul class="contact">
        <li>
          <svg viewBox="0 0 12 12" aria-hidden="true"><path d="M2.4 0.6 4.3 2.5 3.3 4c.7 1.5 2 2.8 3.5 3.6l1.5-1 1.9 1.9-1.2 1.9C5.4 10.3 1.2 6.1.6 2z"/></svg>
          <span>055-987 654 321</span>
        </li>
        <li>
          <svg viewBox="0 0 12 12" aria-hidden="true"><path d="M3 0h5v3H3z M1 4h10v7H1z M3 6h2v1H3z M6 6h2v1H6z M3 8h2v1H3z M6 8h2v1H6z"/></svg>
          <span>055-987 654 321</span>
        </li>
        <li>
          <svg viewBox="0 0 12 12" aria-hidden="true"><path d="M1 2.5h10v7H1z" opacity=".9"/><path d="M1 2.5 6 6.5l5-4" fill="none" stroke="#5b97d2" stroke-width="1"/></svg>
          <span>hello@brightmere.com</span>
        </li>
      </ul>
    </div>
  </section>

  <section class="card card--back" aria-label="Business card back">
    <div class="card__frost">
      <div class="wordmark wordmark--ghost" aria-hidden="true">
        <span class="wordmark__dot"></span>
        <span class="wordmark__name">Brightmere</span>
      </div>
    </div>
    <div class="card__band">
      <p class="site">WWW.BRIGHTMERE.COM</p>
    </div>
  </section>

</main>
</body>
</html>
```